Exclusive Crestline Groomers Invite that connects barbers

I am looking for a general invitation to join a secret club of people that shave their head. I want it the size of a business card that I can hand out to people I see on the street. I want it to feel like a special exclulisve invite to a club that only they can be apart of and want to tell their friends about.

Target Market(s)

35-60 male

Industry/Entity Type

Hair

Contact Information for Business Card

I want it to look like an invite to a secret club that only people that shave their head can be apart of... I will hand it out to people that I think fir our demographic.

Font styles to use
Serif

Colors

Designer to choose colors to be used in the design.

Requirements
Must have
• A feel of exclusivity
• website address (www.crestlinegroomers.example)
• logo

```html
<!DOCTYPE html>
<html lang="en">
<head>
<meta charset="utf-8">
<title>Crestline Groomers – Members' Invitation Cards</title>
<link href="https://fonts.googleapis.com/css2?family=Cinzel:wght@600;700&family=Lora:wght@400;600&display=swap" rel="stylesheet">
<style>
  :root {
    --stage: #e9e6e2;
    --card-white: #ffffff;
    --ink: #1c1c1c;
    --charcoal: #1e1e1e;
    --rose: #d4978a;
    --paper-light: #f3e2cd;
    --paper-dark: #d9b98f;
    --text-light: #ffffff;
  }
  * { box-sizing: border-box; margin: 0; padding: 0; }
  html, body { width: 1200px; height: 900px; overflow: hidden; }
  body {
    background: var(--stage);
    font-family: "Lora", Georgia, serif;
    position: relative;
  }
  .card { position: absolute; overflow: hidden; box-shadow: 0 6px 18px rgba(0,0,0,.18); }

  /* Front card */
  .card-front { left: 78px; top: 34px; width: 588px; height: 364px; background: var(--card-white); }
  .card-front .shapes { position: absolute; inset: 0; }
  .brand-name {
    position: absolute; left: 0; right: 0; top: 84px;
    text-align: center; font-family: "Cinzel", Georgia, serif;
    font-weight: 700; font-size: 30px; line-height: 44px;
    color: var(--ink); letter-spacing: 1px;
  }
  .contact-list {
    position: absolute; left: 30px; top: 254px; list-style: none;
    color: var(--text-light); font-size: 14px;
  }
  .contact-list li { display: flex; align-items: center; height: 21.5px; white-space: nowrap; }
  .contact-list svg {
    width: 12px; height: 12px; margin-right: 9px; flex: none;
    fill: none; stroke: var(--text-light); stroke-width: 1.4;
  }
  .holder { position: absolute; right: 36px; top: 236px; text-align: right; color: var(--text-light); }
  .holder-name { font-size: 22px; font-weight: 600; line-height: 28px; }
  .holder-role { font-size: 14px; line-height: 20px; }
  .holder-address { font-size: 14px; line-height: 21px; margin-top: 10px; }

  /* Back card */
  .card-back {
    left: 388px; top: 505px; width: 567px; height: 352px;
    background: radial-gradient(ellipse at 50% 45%, var(--paper-light) 0%, var(--paper-dark) 100%);
    text-align: center;
  }
  .back-mark {
    position: absolute; left: 253px; top: 118px; width: 60px; height: 60px;
    background: var(--charcoal); border-radius: 6px;
  }
  .back-name {
    position: absolute; left: 0; right: 0; top: 206px;
    font-family: "Cinzel", Georgia, serif; font-weight: 700;
    font-size: 28px; line-height: 40px; letter-spacing: 1px; color: var(--ink);
  }
  .back-url {
    position: absolute; left: 0; right: 0; top: 290px;
    font-size: 14px; letter-spacing: 1px; color: var(--ink);
  }
</style>
</head>
<body>
  <section class="card card-front">
    <svg class="shapes" viewBox="0 0 588 364" width="588" height="364" aria-hidden="true">
      <polygon points="0,199 382,199 358,226 0,226" fill="var(--rose)"/>
      <polygon points="0,230 364,230 396,191 588,191 588,364 0,364" fill="var(--charcoal)"/>
    </svg>
    <div class="brand-name">Crestline Groomers</div>
    <ul class="contact-list">
      <li><svg viewBox="0 0 12 12"><rect x="3" y="0.7" width="6" height="10.6" rx="1.2"/><line x1="5" y1="9.3" x2="7" y2="9.3"/></svg>044-555 010 200</li>
      <li><svg viewBox="0 0 12 12"><path d="M1 5.5C1 2 11 2 11 5.5"/><rect x="2.5" y="6.5" width="7" height="4.5" rx="0.8"/></svg>044-555 010 200</li>
      <li><svg viewBox="0 0 12 12"><rect x="0.7" y="2.2" width="10.6" height="7.6"/><path d="M0.7 2.2L6 6.5l5.3-4.3"/></svg>info@crestlinegroomers.example</li>
      <li><svg viewBox="0 0 12 12"><circle cx="6" cy="6" r="5.2"/><ellipse cx="6" cy="6" rx="2.2" ry="5.2"/><line x1="0.8" y1="6" x2="11.2" y2="6"/></svg>www.crestlinegroomers.example</li>
    </ul>
    <div class="holder">
      <div class="holder-name">Marcus Hale</div>
      <div class="holder-role">Managing Director</div>
      <div class="holder-address">12345, Address Goes Here<br>Country Name, 123456.</div>
    </div>
  </section>

  <section class="card card-back">
    <div class="back-mark"></div>
    <div class="back-name">Crestline Groomers</div>
    <div class="back-url">www.crestlinegroomers.example</div>
  </section>
</body>
</html>
```